High-end construction company needs a business card design

We need a modern looking business card that draws people in, is memorable and looks so good people will want to sick it on their fridges.
On the first side what is needed are:
Logo
My name - Tomasz Brelwik
Title - Managing Director
Website - www.varkelt.co.uk
Email - tomasz@varkelt.co.uk
Telephone - 020 5194 6281
Mobile - 07845139072
On the back side was is needed is a list of all the services we provide:
-Kitchen Renovations
-Bathroom Renovations
-House Renovations
-Garage Conversions
-Extensions
-Loft Conversions
-Conservatories
-Carpentry
-Tiling
-Electrical
-Plumbing & Heating
-Bricklaying
-Landscaping
-Decorating
-Plastering
We would like the colours to be the same shades as on the logo with grey or black for the words.
Target Market(s)
Anyone who needs building work done
Contact Information for Business Card
This business card is for a construction company which strives to deliver excellent service and quality.
The look and feel of the card should represent this.
Requirements
Must have
- On the first side what is needed are:
Logo
My name - Tomasz Brelwik
Title - Managing Director
Website - www.varkelt.co.uk
Email - tomasz@varkelt.co.uk
Telephone - 020 5194 6281
Mobile - 07845139072
Nice to have
- Cool looking features

```html
<!DOCTYPE html>
<html lang="en">
<head>
<meta charset="utf-8">
<title>Varkelt Construction Ltd – Business Card</title>
<link href="https://fonts.googleapis.com/css2?family=Montserrat:wght@400;500;600;700&display=swap" rel="stylesheet">
<style>
  :root {
    --green-dark: #4a8c3f;
    --green-light: #6cbf46;
    --white: #ffffff;
    --page: #e9ebe8;
    --card-w: 720px;
    --card-h: 411px;
  }
  * { box-sizing: border-box; margin: 0; padding: 0; }
  html, body {
    width: 1200px; height: 900px; overflow: hidden;
    background: var(--page);
    font-family: "Montserrat", sans-serif;
  }
  .card {
    position: absolute; left: 240px;
    width: var(--card-w); height: var(--card-h);
    overflow: hidden;
    box-shadow: 0 6px 18px rgba(0,0,0,.18);
  }
  .card--services { top: 26px; background: var(--green-dark); color: var(--white); }
  .card--contact  { top: 463px; background: var(--green-dark); }

  /* services side */
  .services-brand {
    position: absolute; top: 78px; left: 0; right: 0;
    text-align: center; font-weight: 700; color: var(--white);
    line-height: 1.05;
  }
  .brand-name { display: block; font-size: 58px; letter-spacing: 2px; }
  .brand-sub  { display: block; font-size: 18px; letter-spacing: 5px; }
  .services-list {
    position: absolute; top: 230px; left: 30px; right: 30px;
    text-align: center; font-size: 17px; font-weight: 400; line-height: 1.55;
    list-style: none;
  }

  /* contact side */
  .contact-arc { position: absolute; inset: 0; }
  .contact-block {
    position: absolute; top: 46px; left: 56px; color: var(--white);
  }
  .contact-accent {
    position: absolute; left: -56px; top: 4px; width: 9px; height: 26px;
    background: var(--green-light);
  }
  .contact-name { font-size: 25px; font-weight: 700; }
  .contact-title { font-size: 16px; font-weight: 400; margin-top: 2px; }
  .contact-address { font-size: 16px; margin-top: 22px; line-height: 1.35; }
  .contact-lines { list-style: none; margin-top: 18px; font-size: 16px; line-height: 1.55; }
  .contact-lines li { display: flex; align-items: center; gap: 8px; }
  .contact-lines svg { width: 13px; height: 13px; flex: none; }
  .contact-brand {
    position: absolute; left: 400px; top: 140px; width: 300px;
    text-align: center; font-weight: 700; color: var(--green-dark); line-height: 1.05;
  }
  .contact-brand .brand-name { font-size: 50px; }
  .contact-brand .brand-sub { font-size: 16px; letter-spacing: 4px; }
</style>
</head>
<body>

<section class="card card--services" aria-label="Services side">
  <div class="services-brand">
    <span class="brand-name">VARKELT</span>
    <span class="brand-sub">CONSTRUCTION LTD</span>
  </div>
  <ul class="services-list">
    <li>Kitchen Renovations | Bathroom Renovations</li>
    <li>House Renovations | Garage Conversions | Extensions</li>
    <li>Loft Conversions | Conservatories | Carpentry | Tiling | Electrical</li>
    <li>Plumbing &amp; Heating | Bricklaying | Landscaping | Decorating | Plastering</li>
  </ul>
</section>

<section class="card card--contact" aria-label="Contact side">
  <svg class="contact-arc" viewBox="0 0 720 411" aria-hidden="true">
    <path d="M470 0 C 300 40, 300 360, 520 411 L720 411 L720 0 Z" fill="#6cbf46"/>
    <path d="M486 0 C 330 50, 330 360, 540 411 L720 411 L720 0 Z" fill="#4a8c3f"/>
    <path d="M500 0 C 350 55, 350 360, 560 411 L720 411 L720 0 Z" fill="#ffffff"/>
  </svg>

  <div class="contact-block">
    <span class="contact-accent"></span>
    <h1 class="contact-name">Tomasz Brelwik</h1>
    <p class="contact-title">Managing Director</p>
    <p class="contact-address">14-16 Harrow Lane,<br>London, N4 2RT</p>
    <ul class="contact-lines">
      <li><svg viewBox="0 0 16 16"><path d="M4 1l3 3-2 2c1 2 3 4 5 5l2-2 3 3-2 3C7 15 1 9 1 3z" fill="#fff"/></svg>020 5194 6281</li>
      <li><svg viewBox="0 0 16 16"><rect x="4" y="1" width="8" height="14" rx="1.5" fill="none" stroke="#fff" stroke-width="1.6"/><circle cx="8" cy="12.5" r="1" fill="#fff"/></svg>07845139072</li>
      <li><svg viewBox="0 0 16 16"><rect x="1" y="3" width="14" height="10" fill="none" stroke="#fff" stroke-width="1.6"/><path d="M1 3l7 6 7-6" fill="none" stroke="#fff" stroke-width="1.6"/></svg>tomasz@varkelt.co.uk</li>
      <li><svg viewBox="0 0 16 16"><circle cx="8" cy="8" r="6.5" fill="none" stroke="#fff" stroke-width="1.4"/><path d="M1.5 8h13M8 1.5c-3 3-3 10 0 13M8 1.5c3 3 3 10 0 13" fill="none" stroke="#fff" stroke-width="1.2"/></svg>www.varkelt.co.uk</li>
    </ul>
  </div>

  <div class="contact-brand">
    <span class="brand-name">VARKELT</span>
    <span class="brand-sub">CONSTRUCTION LTD</span>
  </div>
</section>

</body>
</html>
```